Business card for event manager / organizer "waiter service"

Draft of a new valuable business card for my company.
Events, personnel service providers, festivals

```html
<!DOCTYPE html>
<html lang="de">
<head>
<meta charset="utf-8">
<title>Lenno´s Kellnerservice – Visitenkarte</title>
<link href="https://fonts.googleapis.com/css2?family=Montserrat:wght@700&family=Poppins:wght@400&display=swap" rel="stylesheet">
<style>
  :root {
    --page: #e8e2db;
    --card-dark: #111010;
    --card-mid: #1e1c1b;
    --accent: #cf6a1f;
    --text: #e6ddd3;
    --muted: #c9bfb4;
  }
  html, body {
    margin: 0;
    width: 1200px;
    height: 1047px;
    overflow: hidden;
    background: var(--page);
  }
  .card {
    position: absolute;
    left: 80px;
    top: 240px;
    width: 1040px;
    height: 567px;
    border-radius: 26px;
    overflow: hidden;
    background: linear-gradient(100deg, var(--card-mid) 0%, var(--card-dark) 45%, #0c0b0b 100%);
    box-shadow: 0 20px 50px rgba(0,0,0,0.25);
  }
  .portrait {
    position: absolute;
    left: 0;
    top: 0;
    width: 420px;
    height: 100%;
    background:
      linear-gradient(90deg, rgba(17,16,16,0) 55%, var(--card-dark) 100%),
      radial-gradient(ellipse at 45% 35%, #8a8784 0%, #4a4745 40%, #232120 80%);
  }
  .content {
    position: absolute;
    left: 445px;
    top: 66px;
    right: 30px;
  }
  .brand {
    display: flex;
    align-items: center;
    gap: 12px;
    height: 56px;
  }
  .brand-square {
    width: 22px;
    height: 22px;
    background: var(--accent);
    flex: none;
  }
  .brand-name {
    font-family: "Montserrat", sans-serif;
    font-weight: 700;
    font-size: 26px;
    color: var(--accent);
    letter-spacing: 0.3px;
  }
  .person-name {
    font-family: "Montserrat", sans-serif;
    font-weight: 700;
    font-size: 38px;
    color: var(--accent);
    margin: 74px 0 0;
    line-height: 1;
  }
  .person-role {
    font-family: "Poppins", sans-serif;
    font-size: 25px;
    color: var(--muted);
    margin: 14px 0 0;
  }
  .contacts {
    list-style: none;
    margin: 30px 0 0;
    padding: 0;
    font-family: "Poppins", sans-serif;
    font-size: 26px;
    color: var(--text);
  }
  .contacts li {
    display: flex;
    align-items: center;
    gap: 12px;
    height: 37.5px;
    white-space: nowrap;
  }
  .contacts svg {
    width: 22px;
    height: 22px;
    fill: var(--accent);
    flex: none;
  }
</style>
</head>
<body>
  <div class="card">
    <div class="portrait" role="img" aria-label="Foto des Inhabers in Kellneruniform mit Tablett und Sektgläsern"></div>
    <div class="content">
      <div class="brand">
        <div class="brand-square"></div>
        <div class="brand-name">LENNO´S KELLNERSERVICE</div>
      </div>
      <p class="person-name">Lenno Brandt</p>
      <p class="person-role">Inhaber</p>
      <ul class="contacts">
        <li>
          <svg viewBox="0 0 24 24"><path d="M3 9c0-3 4-5 9-5s9 2 9 5v2h-5V9c-1-1-7-1-8 0v2H3z M6 12h12l2 8H4z M12 14a2.5 2.5 0 1 0 0 5a2.5 2.5 0 1 0 0-5z"/></svg>
          02361 555 12 40
        </li>
        <li>
          <svg viewBox="0 0 24 24"><path d="M3 9c0-3 4-5 9-5s9 2 9 5v2h-5V9c-1-1-7-1-8 0v2H3z M6 12h12l2 8H4z M12 14a2.5 2.5 0 1 0 0 5a2.5 2.5 0 1 0 0-5z"/></svg>
          0170 555 48 21
        </li>
        <li>
          <svg viewBox="0 0 24 24"><circle cx="12" cy="12" r="10"/><path d="M7 8l3 1 1 3-2 2 1 4-3-3-1-4z M14 5l3 2-1 3 3 2-2 4-2-2v-3l-2-2z" fill="#111"/></svg>
          www.lennos-kellnerservice.de
        </li>
        <li>
          <svg viewBox="0 0 24 24"><path d="M2 6h20v13H2z"/><path d="M2 6l10 7 10-7" fill="none" stroke="#111" stroke-width="1.8"/></svg>
          info@lennos-kellnerservice.de
        </li>
        <li>
          <svg viewBox="0 0 24 24"><path d="M12 2a7 7 0 0 0-7 7c0 5 7 13 7 13s7-8 7-13a7 7 0 0 0-7-7z"/><circle cx="12" cy="9" r="2.6" fill="#111"/></svg>
          Lindenweg 12, 45700 Musterstadt
        </li>
        <li>
          <svg viewBox="0 0 24 24"><rect x="3" y="3" width="18" height="18" rx="2"/></svg>
          www.treffpunkt.de/lennoskellnerservice
        </li>
      </ul>
    </div>
  </div>
</body>
</html>
```